Thornbury Building Company - Card Design

I am looking to use the logo designs that you already did for me to develop a business card. I would like the card to have a black background and be double sided. I want white and green logo and text. I have attached an inspiration photo of a look that I like. I would like to use the Vertical Logo attached to take up the full front side of the card. On the back where I have my name and information, I would like to have the horizontal logo or maybe even just the image of the 'A' and trees without the text. I am open, but I am looking for something clean and simple and I want the green to really pop! Additional files can be found under Design #: 58302946

Target Market(s)

Homeowners

Industry/Entity Type

Construction

Contact Information for Business Card

Name: Marcus Thornbury, Title: Project Manager, Phone: 555.274.8136, Email: thornburybuildingcompany@mailvesta.com, address: 487 Larkspur Ln, Brookhaven, CA 95033, Lic# 2468317

Colors
00AB8E
00BBA5
67D7C9
C6EFE9
E9F9F6

Requirements
Nice to have
• I would like to see the logos that I have already got from ArtLoomHub, though I am open to new ones

```html
<!DOCTYPE html>
<html lang="en">
<head>
<meta charset="utf-8">
<title>Thornbury Building Company – Business Card</title>
<link rel="stylesheet" href="https://fonts.googleapis.com/css2?family=Montserrat:wght@400;500;600;700&display=swap">
<style>
  :root {
    --backdrop: #e7e4df;
    --card: #262626;
    --card-deep: #1c1c1c;
    --green: #6cb644;
    --white: #ffffff;
    --soft-white: #e6e6e6;
    --sheen: rgba(255, 255, 255, 0.05);
  }
  * { box-sizing: border-box; margin: 0; padding: 0; }
  html, body {
    width: 900px;
    height: 1200px;
    overflow: hidden;
    background: var(--backdrop);
    font-family: "Montserrat", Arial, sans-serif;
  }
  .canvas { position: relative; width: 900px; height: 1200px; }
  .card {
    position: absolute;
    left: 80px;
    width: 742px;
    height: 442px;
    border-radius: 28px;
    background: var(--card);
    overflow: hidden;
    color: var(--white);
  }
  .card--front { top: 130px; }
  .card--back { top: 638px; }
  .card__sheen {
    position: absolute;
    inset: 0;
    background: linear-gradient(120deg, transparent 50%, var(--sheen) 70%, transparent 90%),
                linear-gradient(180deg, var(--card) 0%, var(--card-deep) 100%);
  }
  .wordmark {
    position: absolute;
    display: flex;
    align-items: center;
    gap: 18px;
    font-weight: 700;
    color: var(--white);
    letter-spacing: 0.04em;
    text-transform: uppercase;
    line-height: 1.05;
  }
  .wordmark__square { background: var(--green); flex: none; }
  .wordmark__sub { display: block; font-size: 0.5em; letter-spacing: 0.24em; }
  .card--front .wordmark { left: 38px; top: 132px; font-size: 40px; }
  .card--front .wordmark__square { width: 44px; height: 44px; }
  .card--back .wordmark { left: 80px; top: 168px; font-size: 54px; }
  .card--back .wordmark__square { width: 70px; height: 70px; }

  .contact { position: absolute; left: 38px; top: 236px; }
  .contact__name { font-size: 25px; font-weight: 700; color: var(--green); }
  .contact__title { font-size: 16px; color: var(--soft-white); margin-top: 2px; }
  .contact__licence { font-size: 16px; font-weight: 600; margin-top: 20px; }
  .contact__licence span { color: var(--green); font-weight: 500; }
  .contact__list { list-style: none; margin-top: 14px; }
  .contact__item {
    display: flex; align-items: center; gap: 12px;
    font-size: 15.5px; color: var(--soft-white); height: 27px;
  }
  .contact__item svg { width: 14px; height: 14px; fill: var(--green); flex: none; }
</style>
</head>
<body>
<main class="canvas">
  <section class="card card--front" aria-label="Card front">
    <div class="card__sheen"></div>
    <div class="wordmark">
      <span class="wordmark__square"></span>
      <span>Thornbury<span class="wordmark__sub">Building Company</span></span>
    </div>
    <div class="contact">
      <p class="contact__name">Marcus Thornbury</p>
      <p class="contact__title">Project Manager</p>
      <p class="contact__licence"><span>Lic</span> #2468317</p>
      <ul class="contact__list">
        <li class="contact__item">
          <svg viewBox="0 0 24 24"><path d="M12 2a7 7 0 0 0-7 7c0 5 7 13 7 13s7-8 7-13a7 7 0 0 0-7-7zm0 9.5A2.5 2.5 0 1 1 12 6.5a2.5 2.5 0 0 1 0 5z"/></svg>
          487 Larkspur Ln, Brookhaven, CA 95033
        </li>
        <li class="contact__item">
          <svg viewBox="0 0 24 24"><path d="M6.6 10.8a15 15 0 0 0 6.6 6.6l2.2-2.2a1 1 0 0 1 1-.25 11.4 11.4 0 0 0 3.6.57 1 1 0 0 1 1 1V20a1 1 0 0 1-1 1A17 17 0 0 1 3 4a1 1 0 0 1 1-1h3.5a1 1 0 0 1 1 1c0 1.25.2 2.45.57 3.57a1 1 0 0 1-.25 1z"/></svg>
          555.274.8136
        </li>
        <li class="contact__item">
          <svg viewBox="0 0 24 24"><path d="M2 5h20v2l-10 6L2 7zM2 9l10 6 10-6v10H2z"/></svg>
          thornburybuildingcompany@mailvesta.com
        </li>
      </ul>
    </div>
  </section>

  <section class="card card--back" aria-label="Card back">
    <div class="card__sheen"></div>
    <div class="wordmark">
      <span class="wordmark__square"></span>
      <span>Thornbury<span class="wordmark__sub">Building Company</span></span>
    </div>
  </section>
</main>
</body>
</html>
```